Billboard design 8x3M RAVU (Spanish company)

We´re located in the south of Spain. We run a local telecom company.
We sell Fiber optic, and mobile phone lines mainly.
The billboard will have to be in Spanish, I would like the price to be something you spot on first sight when passing by in the car.
Our company color is blue, like in our logo which I will add. I will also add a example from what we currently have.
The new offer should be:
1000 megas + 100Gigas movil con llamadas ilimitadas. (meaning 1000Mb fiber optic speed and 100Gb data and unlimited calls for 1 mobile line)
Our details are: phone line 958 47 6620
Website: ra-vu.es

```html
<!DOCTYPE html>
<html lang="es">
<head>
<meta charset="utf-8">
<title>RAVU – Valla 8x3</title>
<link rel="stylesheet" href="https://fonts.googleapis.com/css2?family=Urbanist:wght@500;700;800&family=Jost:wght@500&display=swap">
<style>
  :root {
    --page: #e9e5e3;
    --night: #030a17;
    --night-mid: #071a33;
    --glow: #0d3d78;
    --brand-blue: #2a9fd8;
    --teal: #1e5f7d;
    --badge-top: #2f86b8;
    --badge-bottom: #13527d;
    --white: #ffffff;
    --photo-light: #d9d9d9;
    --photo-dark: #4a4a4a;
  }
  * { margin: 0; padding: 0; box-sizing: border-box; }
  html, body { width: 1200px; height: 1075px; overflow: hidden; background: var(--page); }
  .billboard {
    position: absolute; left: 40px; top: 327px; width: 1120px; height: 420px;
    overflow: hidden; color: var(--white);
    font-family: "Urbanist", sans-serif;
    background:
      radial-gradient(ellipse 520px 200px at 880px 340px, rgba(13,61,120,.75), transparent 70%),
      radial-gradient(ellipse 420px 160px at 250px 250px, rgba(7,26,51,.8), transparent 70%),
      var(--night);
    box-shadow: 0 24px 40px rgba(0,0,0,.25);
  }
  .decor { position: absolute; inset: 0; }
  .brand { position: absolute; left: 102px; top: 70px; width: 210px; }
  .brand-name { font-weight: 800; font-size: 66px; line-height: 1; letter-spacing: 4px; }
  .brand-services { font-family: "Jost", sans-serif; font-weight: 500; font-size: 18px; margin-top: 8px; white-space: nowrap; }
  .big-number { position: absolute; font-weight: 700; line-height: 1; letter-spacing: -4px; }
  .fiber-speed { left: 88px; top: 184px; font-size: 116px; }
  .mobile-data { left: 650px; top: 148px; font-size: 116px; }
  .unit-badge {
    position: absolute; display: flex; align-items: center; justify-content: center;
    font-weight: 800; border: 1px solid rgba(140,200,240,.8); border-radius: 3px;
    background: linear-gradient(180deg, var(--badge-top), var(--badge-bottom));
  }
  .unit-megas { left: 101px; top: 291px; width: 184px; height: 61px; font-size: 42px; }
  .unit-gigas { left: 846px; top: 171px; width: 183px; height: 71px; font-size: 46px; }
  .offer-pill {
    position: absolute; left: 640px; top: 68px; width: 373px; height: 48px;
    border: 1.5px solid var(--brand-blue); border-radius: 8px;
    display: flex; align-items: center; justify-content: center;
    font-weight: 500; font-size: 22px;
  }
  .plus { position: absolute; left: 640px; top: 128px; width: 31px; height: 31px; }
  .person-photo {
    position: absolute; left: 356px; top: 39px; width: 268px; height: 344px;
    border-radius: 120px 120px 40px 40px;
    background: linear-gradient(180deg, var(--photo-light) 0%, #bcbcbc 55%, var(--photo-dark) 85%, var(--photo-light) 100%);
    opacity: .9;
  }
  .contact { position: absolute; display: flex; align-items: center; }
  .contact-phone { left: 663px; top: 278px; font-weight: 700; font-size: 50px; gap: 14px; }
  .contact-web { left: 686px; top: 330px; font-weight: 800; font-size: 28px; gap: 16px; }
</style>
</head>
<body>
  <section class="billboard">
    <svg class="decor" width="1120" height="420" viewBox="0 0 1120 420" aria-hidden="true">
      <circle cx="1190" cy="-20" r="200" fill="none" stroke="var(--teal)" stroke-width="22" opacity=".8"/>
      <circle cx="485" cy="530" r="150" fill="none" stroke="var(--teal)" stroke-width="18"/>
    </svg>

    <div class="brand">
      <div class="brand-name">RAVU</div>
      <div class="brand-services">Wifi | Fibra | Movil | Tv</div>
    </div>

    <div class="big-number fiber-speed">1000</div>
    <div class="unit-badge unit-megas">Megas</div>

    <div class="person-photo" role="img" aria-label="Fotografía de un joven sonriente con jersey blanco sentado con las piernas cruzadas y un portátil"></div>

    <div class="offer-pill">movil con llamadas ilimitadas.</div>
    <svg class="plus" viewBox="0 0 31 31" aria-hidden="true">
      <rect x="11" y="0" width="9" height="31" fill="var(--brand-blue)"/>
      <rect x="0" y="11" width="31" height="9" fill="var(--brand-blue)"/>
    </svg>
    <div class="big-number mobile-data">100</div>
    <div class="unit-badge unit-gigas">Gigas</div>

    <div class="contact contact-phone">
      <svg width="36" height="36" viewBox="0 0 24 24" aria-hidden="true">
        <path fill="var(--brand-blue)" d="M6.6 10.8a15.1 15.1 0 0 0 6.6 6.6l2.2-2.2c.3-.3.7-.4 1-.2 1.1.4 2.3.6 3.6.6.6 0 1 .4 1 1V20c0 .6-.4 1-1 1C10.6 21 3 13.4 3 4c0-.6.4-1 1-1h3.5c.6 0 1 .4 1 1 0 1.3.2 2.5.6 3.6.1.3 0 .7-.2 1z"/>
      </svg>
      <span>958-47-6620</span>
    </div>
    <div class="contact contact-web">
      <svg width="14" height="18" viewBox="0 0 14 18" aria-hidden="true">
        <path fill="var(--brand-blue)" d="M0 0l13 10-6 .5 3.5 6.5-2.3 1-3.4-6.6L0 16z"/>
      </svg>
      <span>ra-vu.es</span>
    </div>
  </section>
</body>
</html>
```